Brovanek Data Yellow rose letterhead

I have a new logo for my company but in its current form it is too large to be used on letterhead or as a email signature. I need to have the designer use elements from the current logo and create something close to the original but more suited for smaller items.
Updates

I just uploaded a copy of our logo that does not have the weathered affect. Thanks

Reason: More time for revisions

Industry/Entity Type

It Company

Requirements
Must have
• The design must maintain the visual effect of the current logo. It needs to include the yellow rose and the name of the company.
Nice to have
• It would be nice to maintain the stamp theme and incorporate my name, address, phone, email. etc.

```html
<!DOCTYPE html>
<html lang="en">
<head>
<meta charset="utf-8">
<title>Brovanek Data Letterhead</title>
<link href="https://fonts.googleapis.com/css2?family=Questrial&display=swap" rel="stylesheet">
<style>
  :root {
    --backdrop: #e9e7e3;
    --paper: #ffffff;
    --teal: #35b5b3;
    --gold: #f6c92f;
    --rose: #f7cd2e;
    --brand-brown: #5a4636;
    --ink: #1c1c1c;
  }
  html, body {
    margin: 0;
    padding: 0;
    width: 1054px;
    height: 1200px;
    overflow: hidden;
    background: var(--backdrop);
  }
  .letterhead {
    position: absolute;
    left: 131px;
    top: 40px;
    width: 791px;
    height: 1120px;
    background: var(--paper);
    overflow: hidden;
  }
  .header-band {
    position: absolute;
    left: 0;
    top: 0;
    width: 791px;
    height: 230px;
  }
  .brand-mark {
    position: absolute;
    left: 62px;
    top: 24px;
    width: 150px;
    height: 150px;
    border-radius: 50%;
    background: var(--rose);
  }
  .brand-name {
    position: absolute;
    left: 19px;
    top: 212px;
    width: 240px;
    margin: 0;
    font-family: "Questrial", sans-serif;
    font-weight: 400;
    font-size: 30px;
    line-height: 38px;
    letter-spacing: 1px;
    text-transform: uppercase;
    text-align: center;
    color: var(--brand-brown);
  }
  .brand-name span { display: block; }
  .contact-block {
    position: absolute;
    left: 462px;
    top: 20px;
    margin: 0;
    font-family: "Questrial", sans-serif;
    font-style: normal;
    color: var(--ink);
  }
  .contact-block .contact-name {
    display: block;
    font-size: 16px;
    line-height: 24px;
  }
  .contact-block .contact-line {
    display: block;
    font-size: 18.5px;
    line-height: 23px;
    letter-spacing: 0.3px;
  }
</style>
</head>
<body>
  <main class="letterhead">
    <svg class="header-band" viewBox="0 0 791 230" aria-hidden="true">
      <path d="M0,188 Q330,150 791,150 L791,174 Q330,168 0,206 Z" fill="var(--gold)"/>
      <path d="M0,182 Q330,142 791,142 L791,166 Q330,160 0,198 Z" fill="var(--teal)"/>
    </svg>

    <div class="brand-mark" aria-hidden="true"></div>
    <h1 class="brand-name"><span>Brovanek</span><span>Data</span></h1>

    <address class="contact-block">
      <span class="contact-name">Mara Ellison, PhD</span>
      <span class="contact-line">412 NE Cedar Ridge Trail, Ste 2108</span>
      <span class="contact-line">Pale Creek, TX 76511</span>
      <span class="contact-line">1-800-555-0142</span>
      <span class="contact-line">mara@brovanek-data.com</span>
    </address>
  </main>
</body>
</html>
```